Business Card Design Project - del varosi group

dear Sirs

we need business card design for our group ( DEL Varosi Group ) , i have got the Logo design of our group from pixel harbor in previous , so all need details relating to our group i think available with you, as well as the the chosen logo design

we hope to provide us with business card logo that to be appropaite and satisfactory to us .

thanks

note : logo design of our group is attached .
Updates

Reason: please extend the deadline of my project for additional 15 days because i didn't received appropriate design for our gruop yet . kindly beaware that i have received 77 design till now , supossed to send me 200-250 design at least . thanks

Target Market(s)

contents

name : Kerem EL Nadiri

position : Operation Manager

Industry/Entity Type

Business

Requirements
Must have

• person name

group logo
Nice to have
• logo color matching with back background

```html
<!DOCTYPE html>
<html lang="en">
<head>
<meta charset="utf-8">
<title>DEL Varosi Group – Business Card</title>
<link rel="stylesheet" href="https://fonts.googleapis.com/css2?family=Arimo:wght@400;700&display=swap">
<style>
  :root {
    --page-bg: #e4e5e8;
    --card-white: #ffffff;
    --card-grey: #f1f2f4;
    --brand-blue: #1c5ea8;
    --brand-navy: #134d8d;
    --brand-gold: #d6a83c;
    --ink-dark: #1d2430;
    --ink-light: #ffffff;
  }
  * { margin: 0; padding: 0; box-sizing: border-box; }
  html, body { width: 1067px; height: 1200px; overflow: hidden; }
  body {
    background: var(--page-bg);
    font-family: "Arimo", Arial, sans-serif;
    position: relative;
  }
  .card {
    position: absolute;
    left: 103px;
    width: 860px;
    height: 491px;
    overflow: hidden;
    box-shadow: 0 6px 18px rgba(0,0,0,0.18);
    background: linear-gradient(135deg, var(--card-white) 0%, var(--card-grey) 100%);
  }
  .card--front { top: 80px; }
  .card--back { top: 630px; }

  /* Front */
  .front-mark {
    position: absolute;
    inset: 0;
    display: flex;
    align-items: center;
    justify-content: center;
    gap: 22px;
  }
  .front-mark__dot {
    width: 46px; height: 46px;
    border-radius: 50%;
    background: var(--brand-gold);
  }
  .front-mark__name {
    font-weight: 700;
    font-size: 56px;
    letter-spacing: 2px;
    color: var(--brand-navy);
  }

  /* Back */
  .back-band { position: absolute; inset: 0; }
  .back-logo {
    position: absolute;
    left: 62px;
    top: 88px;
    display: flex;
    align-items: center;
    gap: 14px;
  }
  .back-logo__dot {
    width: 26px; height: 26px;
    background: var(--brand-gold);
    border-radius: 50%;
  }
  .back-logo__name {
    font-weight: 700;
    font-size: 38px;
    letter-spacing: 1px;
    color: var(--brand-navy);
  }
  .person {
    position: absolute;
    left: 118px;
    top: 262px;
    color: var(--ink-dark);
  }
  .person__name { font-size: 22px; }
  .person__role { font-size: 15px; margin-top: 4px; }
  .person__address {
    margin-top: 26px;
    font-size: 15px;
    line-height: 22px;
  }
  .contacts {
    position: absolute;
    left: 520px;
    top: 200px;
    list-style: none;
    color: var(--ink-light);
    font-size: 15px;
  }
  .contacts li {
    display: flex;
    align-items: center;
    gap: 12px;
    height: 28px;
  }
  .contacts svg { width: 16px; height: 16px; fill: var(--ink-light); flex: none; }
</style>
</head>
<body>

<section class="card card--front" aria-label="Business card front">
  <div class="front-mark">
    <span class="front-mark__dot"></span>
    <span class="front-mark__name">DEL VAROSI GROUP</span>
  </div>
</section>

<section class="card card--back" aria-label="Business card back">
  <svg class="back-band" viewBox="0 0 860 491" preserveAspectRatio="none" aria-hidden="true">
    <polygon points="0,212 80,212 100,232 120,212 860,172 860,491 0,491" fill="var(--brand-blue)"/>
  </svg>

  <div class="back-logo">
    <span class="back-logo__dot"></span>
    <span class="back-logo__name">DEL VAROSI GROUP</span>
  </div>

  <div class="person">
    <p class="person__name">Kerem EL Nadiri</p>
    <p class="person__role">Operation Manager</p>
    <p class="person__address">
      Al Nahda Area - Section 412<br>
      Street 8 - Building 15<br>
      Erbil - Iraq
    </p>
  </div>

  <ul class="contacts">
    <li>
      <svg viewBox="0 0 16 16"><path d="M3 1l3 3-1.5 2c1 2 3 4 5 5L11.5 9.5l3 3-2 2.5C7 14.5 1.5 9 1 3z"/></svg>
      + 964 750 0004418
    </li>
    <li>
      <svg viewBox="0 0 16 16"><path d="M4 0h8a1 1 0 0 1 1 1v14a1 1 0 0 1-1 1H4a1 1 0 0 1-1-1V1a1 1 0 0 1 1-1zm1 2v10h6V2zm3 11a1 1 0 1 0 0 2 1 1 0 0 0 0-2z"/></svg>
      + 222 222 0002222
    </li>
    <li>
      <svg viewBox="0 0 16 16"><path d="M4 1h8v4H4zM1 6h14v7h-3v2H4v-2H1zm4 5v3h6v-3z"/></svg>
      + 333 333 0003333
    </li>
    <li>
      <svg viewBox="0 0 16 16"><path d="M1 3h14v10H1zm1.5 1.2V5l5.5 4 5.5-4v-.8z"/></svg>
      info@delvarosigroup.com
    </li>
    <li>
      <svg viewBox="0 0 16 16"><path d="M8 1a7 7 0 1 0 0 14A7 7 0 0 0 8 1zm0 1.5c.9 0 1.9 1.8 2.1 4.5H5.9C6.1 4.3 7.1 2.5 8 2.5zM2.6 7h1.8c.1-1.6.5-3 1-3.9A5.5 5.5 0 0 0 2.6 7zm0 2a5.5 5.5 0 0 0 2.8 3.9c-.5-.9-.9-2.3-1-3.9zm3.3 0c.2 2.7 1.2 4.5 2.1 4.5s1.9-1.8 2.1-4.5zm5.7 0c-.1 1.6-.5 3-1 3.9A5.5 5.5 0 0 0 13.4 9zm1.8-2a5.5 5.5 0 0 0-2.8-3.9c.5.9.9 2.3 1 3.9z"/></svg>
      www.delvarosigroup.com
    </li>
  </ul>
</section>

</body>
</html>
```